BOLD & MINIMALIST DESIGN NEEDED

We want a very bold but minimalistic business card design that is impactful and utilizes both sides of the business card. Our current logo is included for your use.

We want bold fonts and good use of negative space. We don't want the logo to overpower the design.

Target Market(s)

Professionals who are building new commercial buildings.

Industry/Entity Type

Construction

Contact Information for Business Card

Name, Title, email, office phone, cell phone, website

Font styles to use
Serif
Sans Serif

Requirements
Must have
• Bold design!

```html
<!DOCTYPE html>
<html lang="en">
<head>
<meta charset="utf-8">
<title>Ridgeline Design + Build — Business Card</title>
<link rel="stylesheet" href="https://fonts.googleapis.com/css2?family=Arimo:wght@400;700&display=swap">
<style>
  :root {
    --backdrop: #1c1c1c;
    --card-white: #f3f3f3;
    --brand-green: #7cbd3f;
    --brand-green-light: #a9d77e;
    --ink: #1a1a1a;
    --ink-soft: #333333;
    --paper: #ffffff;
    --paper-shade: #e4e4e4;
  }
  * { margin: 0; padding: 0; box-sizing: border-box; }
  html, body {
    width: 1200px; height: 1059px; overflow: hidden;
    background: var(--backdrop);
    font-family: "Arimo", Arial, sans-serif;
  }
  .canvas { position: relative; width: 1200px; height: 1059px; }

  .card {
    position: absolute;
    border-radius: 24px;
    overflow: hidden;
  }
  .card--front {
    left: 257px; top: 89px; width: 687px; height: 390px;
    background: var(--card-white);
  }
  .card--back {
    left: 254px; top: 546px; width: 693px; height: 395px;
    background: var(--brand-green);
  }

  /* Front */
  .wordmark {
    position: absolute; left: 36px; top: 58px;
    color: var(--ink); font-weight: 700; text-align: center;
    width: 280px;
  }
  .wordmark__name { display: block; font-size: 46px; line-height: 1; letter-spacing: 1px; }
  .wordmark__tag { display: block; font-size: 16px; line-height: 1; letter-spacing: 7px; margin-top: 8px; }

  .brand-mark--front {
    position: absolute; right: 0; bottom: 0; width: 286px; height: 286px;
    background: linear-gradient(90deg, var(--ink) 0%, var(--ink) 40%, var(--brand-green) 60%, var(--brand-green-light) 100%);
  }

  .accent-bar {
    position: absolute; left: 0; top: 185px; width: 20px; height: 41px;
    background: linear-gradient(to bottom, var(--brand-green) 55%, rgba(124,189,63,0.15));
  }
  .person { position: absolute; left: 37px; top: 183px; }
  .person__name { color: var(--brand-green); font-weight: 700; font-size: 26px; line-height: 1.1; }
  .person__title { color: var(--ink-soft); font-size: 18px; line-height: 1.2; margin-top: 2px; }

  .contacts { position: absolute; left: 37px; top: 254px; list-style: none; }
  .contacts li {
    display: flex; align-items: center; gap: 5px;
    height: 26.5px; color: var(--ink-soft); font-size: 19px;
  }
  .contacts svg { width: 13px; height: 13px; flex: none; fill: var(--brand-green); }

  /* Back */
  .brand-mark--back {
    position: absolute; left: 286px; top: 76px; width: 122px; height: 122px;
    background: linear-gradient(90deg, var(--paper-shade), var(--paper) 50%, var(--paper-shade));
  }
  .wordmark--reverse {
    left: 0; top: 236px; width: 100%; color: var(--paper);
  }
  .wordmark--reverse .wordmark__name { font-size: 62px; letter-spacing: 2px; }
  .wordmark--reverse .wordmark__tag { font-size: 23px; letter-spacing: 10px; margin-top: 10px; }
</style>
</head>
<body>
<main class="canvas">

  <section class="card card--front" aria-label="Card front">
    <div class="wordmark">
      <span class="wordmark__name">RIDGELINE</span>
      <span class="wordmark__tag">DESIGN + BUILD</span>
    </div>

    <div class="brand-mark brand-mark--front" role="img" aria-label="Company logo mark"></div>

    <div class="accent-bar"></div>
    <div class="person">
      <p class="person__name">DANA WHITFIELD</p>
      <p class="person__title">Owner/CEO</p>
    </div>

    <ul class="contacts">
      <li>
        <svg viewBox="0 0 16 16" aria-hidden="true"><path d="M3.5 1l2.5 3-1.5 2c1 2 3 4 5 5l2-1.5 3 2.5-1.5 2.5C7 15 1 9 1 2.5z"/></svg>
        07 5120 4480
      </li>
      <li>
        <svg viewBox="0 0 16 16" aria-hidden="true"><path d="M4 0h8a1 1 0 0 1 1 1v14a1 1 0 0 1-1 1H4a1 1 0 0 1-1-1V1a1 1 0 0 1 1-1zm1 2v10h6V2zm3 11a1 1 0 1 0 0 2 1 1 0 0 0 0-2z"/></svg>
        0412 305 967
      </li>
      <li>
        <svg viewBox="0 0 16 16" aria-hidden="true"><path d="M0 3h16v10H0zM1.5 4.5v.3L8 9l6.5-4.2v-.3z"/></svg>
        hello@ridgelinebuild.com
      </li>
      <li>
        <svg viewBox="0 0 16 16" aria-hidden="true"><circle cx="8" cy="8" r="7.5"/></svg>
        www.ridgelinebuild.com
      </li>
    </ul>
  </section>

  <section class="card card--back" aria-label="Card back">
    <div class="brand-mark brand-mark--back" role="img" aria-label="Company logo mark"></div>
    <div class="wordmark wordmark--reverse">
      <span class="wordmark__name">RIDGELINE</span>
      <span class="wordmark__tag">DESIGN + BUILD</span>
    </div>
  </section>

</main>
</body>
</html>
```